we can communicate on this, but i want to follow the approach we took on Pellew|Marsh & Quinlan but i feel the card front needs the black background and the platinum and gold logo. The back? I am open. we can use the same info from PM&Q. Velmont Arc is an enhanced equity investment fund - basically a very exclusive boutique hedge fund that uses only stock options. very advanced things. hope you are interested

Contact Information for Business Card

Dr. Lewis T. Brennick, CFA
Scientifique de fusée financière
701.555.0143
LTBquant47@mailvantor.com

4718 Willow Creek Bend W.
West Fargo, ND 58078

No web site

Colors

Designer to choose colors to be used in the design.

Requirements
Nice to have
• I tend to prefer the most visible applications of the logo to include logo and name, the logo version with a black background and the gold and platinum components separated by the black. I see this working well for a single side (logo and name - this is card front to me).
• I am fairly open to other treatments on the reverse side with the data. To me, it makes sense to have a different color rendition of the logo on the reverse and it may be a muted black tone on tone or an oversized portion that would have spot UV. Or, the reverse may play with colors and layout
Should not have
• Other colors = no no
• Decorative font

```html
<!DOCTYPE html>
<html lang="en">
<head>
<meta charset="utf-8">
<title>Velmont Arc — Business Card</title>
<link href="https://fonts.googleapis.com/css2?family=Open+Sans:wght@400;600;700&family=Roboto:wght@400&display=swap" rel="stylesheet">
<style>
  :root {
    --backdrop: #2a2a2c;
    --card-black: #161618;
    --card-white: #ffffff;
    --gold: #c9a23a;
    --gold-light: #d8b44a;
    --gold-deep: #a8842a;
    --ink: #1c1c1e;
    --ink-soft: #3a3a3c;
    --white: #ffffff;
  }
  * { box-sizing: border-box; margin: 0; padding: 0; }
  html, body {
    width: 1200px; height: 900px; overflow: hidden;
    background: var(--backdrop);
  }
  .canvas { position: relative; width: 1200px; height: 900px; }

  .card {
    position: absolute;
    width: 640px; height: 370px;
    border-radius: 28px;
    box-shadow: 0 18px 40px rgba(0,0,0,.45);
    overflow: hidden;
  }

  /* Front */
  .card-front {
    left: 470px; top: 50px;
    background: var(--card-black);
    display: flex; flex-direction: column; align-items: center; justify-content: center;
    gap: 22px;
  }
  .brand-dot {
    width: 110px; height: 110px; border-radius: 50%;
    background: linear-gradient(135deg, var(--gold-light), var(--gold) 55%, var(--gold-deep));
  }
  .brand-name {
    font-family: "Open Sans", sans-serif;
    font-weight: 700;
    font-size: 46px;
    letter-spacing: 2px;
    color: var(--white);
    text-transform: uppercase;
    white-space: nowrap;
  }

  /* Back */
  .card-back {
    left: 90px; top: 470px;
    background: var(--card-white);
  }
  .name-bar {
    position: absolute; left: 0; top: 44px;
    width: 12px; height: 56px; background: var(--gold);
  }
  .holder { position: absolute; left: 40px; top: 40px; right: 40px; }
  .holder-name {
    font-family: "Open Sans", sans-serif; font-weight: 700;
    font-size: 26px; letter-spacing: 1px; color: var(--gold);
    text-transform: uppercase; line-height: 1.15; white-space: nowrap;
  }
  .holder-role {
    font-family: "Open Sans", sans-serif; font-weight: 600;
    font-size: 19px; color: var(--ink); margin-top: 2px;
  }
  .contact {
    position: absolute; left: 40px; top: 200px;
    font-family: "Roboto", sans-serif; font-size: 17px; color: var(--ink-soft);
    line-height: 1.35;
  }
  .address { margin-bottom: 10px; }
  .contact-row { display: flex; align-items: center; gap: 10px; margin-top: 4px; }
  .contact-row svg { width: 16px; height: 16px; flex: none; fill: var(--gold); }

  .brand-mark {
    position: absolute; right: 40px; bottom: 36px;
    display: flex; flex-direction: column; align-items: center; gap: 12px;
  }
  .brand-mark .brand-dot { width: 74px; height: 74px; }
  .brand-mark .brand-name { font-size: 30px; color: var(--ink); letter-spacing: 1.5px; }
</style>
</head>
<body>
<main class="canvas">
  <section class="card card-front" aria-label="Card front">
    <div class="brand-dot"></div>
    <div class="brand-name">Velmont Arc</div>
  </section>

  <section class="card card-back" aria-label="Card back">
    <div class="name-bar"></div>
    <div class="holder">
      <div class="holder-name">Dr. Lewis T. Brennick, CFA</div>
      <div class="holder-role">Scientifique de fusée financière</div>
    </div>

    <div class="contact">
      <div class="address">4718 Willow Creek Bend W.<br>West Fargo, ND 58078</div>
      <div class="contact-row">
        <svg viewBox="0 0 24 24" aria-hidden="true"><path d="M6.6 10.8a15.1 15.1 0 0 0 6.6 6.6l2.2-2.2c.3-.3.7-.4 1-.2 1.1.4 2.3.6 3.6.6.6 0 1 .4 1 1V20c0 .6-.4 1-1 1A17 17 0 0 1 3 4c0-.6.4-1 1-1h3.5c.6 0 1 .4 1 1 0 1.3.2 2.5.6 3.6.1.3 0 .7-.2 1z"/></svg>
        <span>701.555.0143</span>
      </div>
      <div class="contact-row">
        <svg viewBox="0 0 24 24" aria-hidden="true"><path d="M3 5h18v14H3zm2 2v.4l7 4.6 7-4.6V7zm0 2.8V17h14V9.8l-7 4.6z"/></svg>
        <span>LTBquant47@mailvantor.com</span>
      </div>
    </div>

    <div class="brand-mark">
      <div class="brand-dot"></div>
      <div class="brand-name">Velmont Arc</div>
    </div>
  </section>
</main>
</body>
</html>
```